Permanent Makeup Certificate for Lash Crest Institute Certified Artists

I need a beautifully designed certificate for my students who have successfully obtained my certification for Eyebrow Micropigmentation.

I have attached my sample certificate in InDesign format. This certificate is how I want the Certified Artist Certificate to read. My wording is extremely important for US Insurance reasons. I would like it to be in 11 x 17 inch format for USA printing.

I have also attached samples of certificates from other companies to give you an idea of how fancy I would like it to be. My company colors are pink and white, so I would like the dominant colors to be shades of pink and white. I like pink pastel combines with darker shades of pink and white. If the design calls for another color in addition to pink, that would also be great. I really like the colors in the Vexora Certificate.

I have attached a copy of my signature in .png

Target Market(s)

Beauty Industry

Industry/Entity Type

Artists

Font styles to use
Serif
Script

Colors
ffffff
f9d9e8
9bcb3c
cadf82
e667a6
e34297
eea4c8
b7a5cd

Requirements
Must have
• Wording exactly as I uploaded in InDesign file
Nice to have
• Beautiful images of female face, I am not sure if I like this idea. Just an experiement

```html
<!DOCTYPE html>
<html lang="en">
<head>
<meta charset="utf-8">
<title>Certificate of Excellence – Lash Crest Institute</title>
<link rel="stylesheet" href="https://fonts.googleapis.com/css2?family=Great+Vibes&family=Montserrat:ital,wght@0,400;0,600;1,400&family=Playfair+Display:wght@400;700&display=swap">
<style>
  :root {
    --page-bg: #ecebea;
    --paper: #fbf8f8;
    --paper-tone: #f3ecee;
    --frame-gold: #d9b46a;
    --frame-gold-light: #f4e2b0;
    --frame-pink: #c2185b;
    --band-dark: #a8124f;
    --band-mid: #d0286f;
    --accent-red: #c4203f;
    --brand-pink: #e34297;
    --text-body: #4a4347;
    --line: #8e8388;
    --skin-light: #efd9cc;
    --skin-mid: #d8b3a0;
    --hair-dark: #5b4a44;
  }
  * { box-sizing: border-box; margin: 0; padding: 0; }
  html, body { width: 1200px; height: 1083px; overflow: hidden; background: var(--page-bg); }

  .certificate {
    position: absolute; left: 40px; top: 180px; width: 1120px; height: 724px;
    padding: 14px;
    background: linear-gradient(135deg, var(--frame-gold-light), var(--frame-gold) 30%, var(--frame-pink) 60%, var(--frame-gold) 85%, var(--frame-gold-light));
    box-shadow: 0 8px 30px rgba(0,0,0,.18);
  }
  .certificate__paper {
    position: relative; width: 100%; height: 100%; overflow: hidden;
    background: radial-gradient(ellipse at 35% 50%, var(--paper) 40%, var(--paper-tone) 100%);
    outline: 2px solid var(--frame-gold); outline-offset: -8px;
  }

  .portrait {
    position: absolute; right: 0; top: 0; width: 440px; height: 100%;
    background: linear-gradient(180deg, var(--hair-dark) 0%, var(--skin-mid) 28%, var(--skin-light) 60%, var(--skin-mid) 100%);
    -webkit-mask-image: linear-gradient(90deg, transparent 0%, #000 22%);
    mask-image: linear-gradient(90deg, transparent 0%, #000 22%);
  }

  .brand { position: absolute; left: 0; width: 690px; top: 44px; text-align: center; }
  .brand__brow {
    width: 230px; height: 38px; margin: 0 auto 12px;
    background: linear-gradient(90deg, transparent, #3a3336 30%, #3a3336 70%, transparent);
    border-radius: 50% 50% 10% 10%; opacity: .75;
  }
  .brand__name {
    display: inline-flex; align-items: center; gap: 12px;
    font-family: "Playfair Display", serif; font-size: 36px; color: var(--brand-pink);
  }
  .brand__dot { width: 12px; height: 12px; border-radius: 50%; background: var(--brand-pink); }

  .title-band {
    position: absolute; left: 0; top: 180px; width: 730px; height: 118px;
    background: linear-gradient(180deg, var(--band-dark), var(--band-mid) 50%, var(--band-dark));
    border-top: 3px solid var(--frame-gold); border-bottom: 3px solid var(--frame-gold);
    display: flex; align-items: center; justify-content: center;
  }
  .title-band__rule { position: absolute; left: 40px; right: 40px; height: 1px; background: var(--frame-gold-light); }
  .title-band__rule--top { top: 14px; }
  .title-band__rule--bottom { bottom: 14px; }
  .title-band__text {
    font-family: "Great Vibes", cursive; font-size: 66px; color: #fff; line-height: 1;
  }

  .certify {
    position: absolute; left: 0; width: 690px; top: 340px; text-align: center;
    font-family: "Playfair Display", serif; font-weight: 700; font-size: 24px;
    letter-spacing: 1px; color: var(--accent-red);
  }
  .statement {
    position: absolute; left: 110px; width: 470px; top: 452px; text-align: center;
    font-family: "Montserrat", sans-serif; font-size: 15px; line-height: 1.5; color: var(--text-body);
  }

  .date {
    position: absolute; left: 110px; top: 590px; width: 210px; text-align: center;
    border-top: 1px solid var(--line); padding-top: 6px;
    font-family: "Montserrat", sans-serif; font-weight: 600; font-size: 14px; color: var(--accent-red);
  }

  .signatory { position: absolute; left: 400px; top: 530px; width: 250px; }
  .signatory__signature {
    height: 48px; margin-bottom: 6px;
    background: linear-gradient(90deg, transparent, rgba(40,30,35,.18) 20%, rgba(40,30,35,.18) 80%, transparent);
    border-radius: 6px;
  }
  .signatory__name {
    border-top: 1px solid var(--line); padding-top: 6px;
    font-family: "Montserrat", sans-serif; font-weight: 600; font-size: 15px; color: var(--accent-red);
  }
  .signatory__role { font-family: "Montserrat", sans-serif; font-size: 13px; color: var(--text-body); }
  .signatory__org { font-family: "Montserrat", sans-serif; font-style: italic; font-size: 13px; color: var(--text-body); }
</style>
</head>
<body>
  <main class="certificate">
    <div class="certificate__paper">
      <div class="portrait" role="img" aria-label="Photograph of a woman with defined eyebrows"></div>

      <header class="brand">
        <div class="brand__brow" role="img" aria-label="Drawn eyebrow illustration"></div>
        <div class="brand__name"><span class="brand__dot"></span>Lash Crest Institute</div>
      </header>

      <div class="title-band">
        <span class="title-band__rule title-band__rule--top"></span>
        <h1 class="title-band__text">Certificate of Excellence</h1>
        <span class="title-band__rule title-band__rule--bottom"></span>
      </div>

      <p class="certify">THIS IS TO CERTIFY THAT</p>

      <p class="statement">Has successfully proven to be an Artist of the Highest Standard in Eyebrow Micropigmentation using the LASH CREST INTERNATIONAL® Microblading Method</p>

      <div class="date">Date</div>

      <div class="signatory">
        <div class="signatory__signature" role="img" aria-label="Handwritten signature"></div>
        <p class="signatory__name">Clara Rose Vance</p>
        <p class="signatory__role">Master Instructor</p>
        <p class="signatory__org">Lash Crest International®</p>
      </div>
    </div>
  </main>
</body>
</html>
```